wardrobe/costume stylist needs good business card for own business

Hi:)

I'm wanting a business card for my company. I am a freelance stylist.

I do wardrobe/costume stylist to TV commercials; Films; Fashion and Lifestyle shoots.

I'd like a design based around my name Rosalind Parfrey written nicely, maybe a colour? Up to you?!

I've attached a couple of images of business cards I like
.... be creative and have fun!

Thank you :)

Reason: I was trying to get my new business card ready for before I headed overseas Friday morning but I don't think that was realistic so I'd like to extend the deadline to give time to the project. Thank you

Hi designers:) Thank you for all your designs, I've extended the deadline until Sunday, so there's a bit more time. I've attached 3 pictures of business cards which I quite like, please take a look to see if it can be of help in your process. I like the pale plain or patterned background with dark font and the dark plain or patterned background with the pale font the motifs the feminine fonts the plain fonts I like the idea of playing with a circle or some shape on one side of the card with my name or initials as in the picture I have on my post could you play around with this idea a bit please? Thank you all for the work you've done :) Rosa

Hi I am working overseas til Saturday night sorry for no feedback until I teturn Thanks :) Rosa

Hi designers, Thank you all so much for submitting your designs, I really appreciate your input into my project :) I'm sorry I didn't get to respond to some comments, and give feedback. I didn't back from being away until later than I expected, and the deadline had passed then, so apologies. Thanks to you all again for all your really good designs :) Rosa

Target Market(s)

I am a freelance stylist my target audience is producers, production companies, photographers, directors...

Industry/Entity Type

Business

Requirements
Must have
• Rosalind Parfrey
Stylist or Wardrobe Stylist

email rosaparfrey@mailbox-example.co.nz
Mobile 0218467193

(Don't have to use the words 'email' and 'mobile')
Nice to have
• Would like it to be double sided
Like B & W
Like pale colour background with dark font or white font
Like dark colour background with pale font
Should not have
• I would prefer it not to incorporate pictures

```html
<!DOCTYPE html>
<html lang="en">
<head>
<meta charset="utf-8">
<title>Rosalind Parfrey — Wardrobe Stylist Business Card</title>
<link rel="stylesheet" href="https://fonts.googleapis.com/css2?family=Yesteryear&family=Roboto+Condensed:wght@400;700&display=swap">
<style>
  :root {
    --stage: #3a3a3c;
    --brand-blue: #2f87cb;
    --ink-light: #ffffff;
    --mark-dark: #1d1d1f;
    --rack-1: #dfe3e8;
    --rack-2: #6f86a3;
    --rack-3: #2f3f5c;
    --rack-4: #c9566a;
    --rack-5: #e9a0a4;
    --card-w: 540px;
    --card-h: 310px;
  }
  * { box-sizing: border-box; margin: 0; padding: 0; }
  html, body {
    width: 1200px; height: 480px; overflow: hidden;
    background: var(--stage);
  }
  .stage {
    width: 1200px; height: 480px;
    display: flex; align-items: center; justify-content: center; gap: 40px;
  }
  .card {
    position: relative;
    width: var(--card-w); height: var(--card-h);
    overflow: hidden;
    box-shadow: 0 10px 24px rgba(0,0,0,.35);
  }
  .rack-photo {
    position: absolute; inset: 0;
    background:
      linear-gradient(180deg, rgba(240,243,247,.85) 0%, rgba(240,243,247,0) 22%),
      linear-gradient(90deg,
        var(--rack-5) 0%, var(--rack-4) 9%, var(--rack-2) 18%,
        var(--rack-3) 30%, var(--rack-2) 42%, var(--rack-4) 52%,
        var(--rack-3) 62%, var(--rack-2) 74%, var(--rack-1) 88%, var(--rack-2) 100%);
    filter: saturate(.75);
  }
  /* front */
  .front .info-panel {
    position: absolute; top: 0; right: 0; bottom: 0;
    width: 51%;
    background: var(--brand-blue);
    border-top-left-radius: 18px;
  }
  .monogram {
    position: absolute;
    width: 78px; height: 78px; border-radius: 50%;
    background: var(--mark-dark);
    display: flex; align-items: center; justify-content: center;
    font-family: "Roboto Condensed", sans-serif;
    font-weight: 700; font-size: 28px; color: var(--ink-light);
    letter-spacing: 1px;
  }
  .front .monogram { left: 26%; top: 57%; transform: translate(-50%, -50%); }
  .details {
    position: absolute; left: 53%; top: 30%;
    color: var(--ink-light);
  }
  .name {
    font-family: "Yesteryear", cursive;
    font-size: 34px; font-weight: 400; line-height: 1;
  }
  .role {
    font-family: "Roboto Condensed", sans-serif;
    font-size: 13px; letter-spacing: .5px; text-transform: uppercase;
    margin-top: 8px;
  }
  .contact-list { list-style: none; margin-top: 18px; }
  .contact-list li {
    display: flex; align-items: center; gap: 9px;
    font-family: "Roboto Condensed", sans-serif;
    font-size: 13px; margin-bottom: 10px;
  }
  .contact-list svg { width: 15px; height: 15px; flex: none; }
  /* back */
  .back .band-top {
    position: absolute; left: 0; right: 0; top: 0; height: 18px;
    background: var(--brand-blue);
  }
  .back .band-bottom {
    position: absolute; left: 0; right: 0; bottom: 0; height: 22px;
    background: var(--brand-blue);
  }
  .back .band-tab {
    position: absolute; left: 42%; width: 22%; bottom: 0; height: 44px;
    background: var(--brand-blue);
    border-radius: 16px 16px 0 0;
  }
  .back .monogram { left: 51%; top: 60%; transform: translate(-50%, -50%); }
</style>
</head>
<body>
<main class="stage">
  <section class="card front" aria-label="Card front">
    <div class="rack-photo" role="img" aria-label="Photo of a clothing rail with colourful garments on hangers"></div>
    <div class="info-panel"></div>
    <div class="monogram">RP</div>
    <div class="details">
      <h1 class="name">Rosalind Parfrey</h1>
      <p class="role">Wardrobe Stylist</p>
      <ul class="contact-list">
        <li>
          <svg viewBox="0 0 16 16" aria-hidden="true"><rect x="1" y="3" width="14" height="10" fill="none" stroke="#fff" stroke-width="1.4"/><path d="M1 3 L8 9 L15 3" fill="none" stroke="#fff" stroke-width="1.4"/></svg>
          rosaparfrey@mailbox-example.co.nz
        </li>
        <li>
          <svg viewBox="0 0 16 16" aria-hidden="true"><rect x="4" y="1" width="8" height="14" rx="1.5" fill="none" stroke="#fff" stroke-width="1.4"/><circle cx="8" cy="12.5" r=".9" fill="#fff"/></svg>
          0218467193
        </li>
      </ul>
    </div>
  </section>

  <section class="card back" aria-label="Card back">
    <div class="rack-photo" role="img" aria-label="Photo of a clothing rail with garments on hangers"></div>
    <div class="band-top"></div>
    <div class="band-tab"></div>
    <div class="band-bottom"></div>
    <div class="monogram">RP</div>
  </section>
</main>
</body>
</html>
```